Design a modern, classy & professional business card for an online real estate agency, specializing in medium-luxury properties in Thailand and later in Singapore and UK.

Possible design ideas so far: (not essential)

- curved corner(s) to the card, white on front & turquoise on back or visa versa.

- front of card - clear and simple, company name in metallic grey/monochrome, logo graphic & company name on front in spot UV or embossed/debossed effect.

- back of card - large, close-cropped, 'ghost' patterns of the C-shaped curves of logo, or company name repeated on back of card in spot UV.

Target Market(s)

- young to middle-aged professionals mainly (but ideally should design should suit all)

- UK, US,EU,AUS & ASIAN mainly (but ideally should design should suit all countries)

Industry/Entity Type

Real Estate

Requirements
Must have
• THEME:
- Luxurious & Modern
- Clean & striking
- Unique & creative

INFO:
- Logo & company name on front
- Contact details on back:

Tobias Hennlund
Managing Director

www.velmontestates.asia
www.velmontestates.co.uk

Tel: 083-274-6159
email: tobias@velmontestates.asia

(contact details can be displayed in any order as suites design.)

Nice to have
• - curved corner(s) to the card, white on front & turquoise on back or visa versa.

Should not have
• - No generic images of properties, palm trees/coconut trees etc.

- No other other bold colors, except for main turquoise, grey, metallic white & black theme.

- No obvious business card templates

```html
<!DOCTYPE html>
<html lang="en">
<head>
<meta charset="utf-8">
<title>Velmont Estates – Business Card</title>
<link rel="stylesheet" href="https://fonts.googleapis.com/css2?family=Cinzel:wght@400;500&display=swap">
<style>
  :root {
    --backdrop: #e6e7e8;
    --card-white: #ffffff;
    --card-shade: #f1f2f2;
    --turquoise: #16c4c1;
    --steel-grey: #7d7e80;
    --soft-grey: #a7a8aa;
    --ink: #3b3c3e;
  }
  * { margin: 0; padding: 0; box-sizing: border-box; }
  html, body {
    width: 1200px; height: 900px; overflow: hidden;
    background: var(--backdrop);
    font-family: "Cinzel", "Times New Roman", serif;
  }
  .stage { position: relative; width: 1200px; height: 900px; }

  .card {
    position: absolute; left: 260px;
    width: 680px; height: 388px;
    border-radius: 30px; overflow: hidden;
    background: linear-gradient(160deg, var(--card-white) 55%, var(--card-shade));
    box-shadow: 0 10px 28px rgba(0,0,0,.12);
  }
  .card-front { top: 42px; }
  .card-back  { top: 470px; }

  .brand { position: absolute; display: flex; flex-direction: column; align-items: center; }
  .brand-square { width: 58px; height: 58px; background: var(--turquoise); }
  .brand-name {
    margin-top: 12px; font-weight: 400; color: var(--steel-grey);
    letter-spacing: .04em; white-space: nowrap;
  }
  .card-front .brand { left: 0; right: 0; top: 112px; }
  .card-front .brand-square { width: 74px; height: 74px; }
  .card-front .brand-name { font-size: 46px; }

  .card-back .wave { position: absolute; inset: 0; }
  .card-back .brand { left: 330px; width: 320px; top: 52px; }
  .card-back .brand-name { font-size: 34px; }

  .holder {
    position: absolute; left: 330px; width: 320px; top: 218px;
    text-align: center; color: var(--ink);
  }
  .holder-name { font-size: 24px; font-weight: 400; letter-spacing: .03em; }
  .holder-role { font-size: 20px; font-weight: 400; margin-top: 6px; letter-spacing: .03em; }

  .contact {
    position: absolute; left: 30px; top: 150px;
    list-style: none; color: var(--card-white);
    font-size: 12.5px; line-height: 17px; letter-spacing: .02em;
  }
  .contact li { display: flex; align-items: flex-start; gap: 8px; }
  .contact svg { flex: none; margin-top: 3px; }
</style>
</head>
<body>
<main class="stage">

  <section class="card card-front" aria-label="Card front">
    <div class="brand">
      <div class="brand-square"></div>
      <span class="brand-name">Velmont Estates</span>
    </div>
  </section>

  <section class="card card-back" aria-label="Card back">
    <svg class="wave" viewBox="0 0 680 388" width="680" height="388" aria-hidden="true">
      <path d="M0,78 C95,28 165,48 225,150 C290,262 380,338 560,346 L680,346 L680,388 L0,388 Z" fill="var(--turquoise)"/>
      <path d="M70,38 C160,20 215,70 262,160 C320,270 420,330 680,330" fill="none" stroke="var(--steel-grey)" stroke-width="9"/>
      <path d="M40,34 C140,2 200,50 248,140 C305,250 405,312 680,318" fill="none" stroke="var(--soft-grey)" stroke-width="3"/>
    </svg>

    <div class="brand">
      <div class="brand-square"></div>
      <span class="brand-name">Velmont Estates</span>
    </div>

    <div class="holder">
      <p class="holder-name">Tobias Hennlund</p>
      <p class="holder-role">Managing Director</p>
    </div>

    <ul class="contact">
      <li>
        <svg width="10" height="10" viewBox="0 0 10 10"><circle cx="5" cy="5" r="5" fill="#fff"/><path d="M2.5,5.2 5,3 7.5,5.2 7.5,7.5 2.5,7.5Z" fill="var(--turquoise)"/></svg>
        <span>Suite # 410, Kell Bldg.<br>BKK 10330</span>
      </li>
      <li>
        <svg width="10" height="10" viewBox="0 0 10 10"><circle cx="5" cy="5" r="5" fill="#fff"/><rect x="3.5" y="2.5" width="3" height="5" rx="1" fill="var(--turquoise)"/></svg>
        <span>083-274-6159</span>
      </li>
      <li>
        <svg width="10" height="10" viewBox="0 0 10 10"><circle cx="5" cy="5" r="5" fill="#fff"/><rect x="3.5" y="2.5" width="3" height="5" rx="1" fill="var(--turquoise)"/></svg>
        <span>083-274-6160</span>
      </li>
      <li>
        <svg width="10" height="10" viewBox="0 0 10 10"><circle cx="5" cy="5" r="5" fill="#fff"/><rect x="2.5" y="3" width="5" height="4" fill="var(--turquoise)"/></svg>
        <span>083-274-6161</span>
      </li>
      <li>
        <svg width="10" height="10" viewBox="0 0 10 10"><circle cx="5" cy="5" r="5" fill="#fff"/><rect x="2.3" y="3.2" width="5.4" height="3.6" fill="var(--turquoise)"/></svg>
        <span>tobias@velmontestates.asia</span>
      </li>
      <li>
        <svg width="10" height="10" viewBox="0 0 10 10"><circle cx="5" cy="5" r="5" fill="#fff"/><circle cx="5" cy="5" r="2.6" fill="none" stroke="var(--turquoise)" stroke-width="1"/></svg>
        <span>www.velmontestates.asia</span>
      </li>
    </ul>
  </section>

</main>
</body>
</html>
```